A New and modern Business Card for Tarwick Trade Solutions Ltd

New and modern Logo and Business Card Attached is the current logo/business card designCurrently the business is called "Tarwick & Co." or TTS Ltd for short. This is subject to change.This business specialises in Telecoms and Energy. We work with the major networks (QV, K7, etc) and also offer Energy Products saving clients money off their energy bills.These are business to business services.The current design incorporates a Pheonix, indicating rebirth, starting something new.We would like to maintain the Phoenix element but a newer modern style.We love colours in the logo 3 max.The aim of this is to be ultra slick and modern. I envisage Tarwick & Co. on one side of the card with long descriptions on the other side.Side 1:TTS Ltd/Logo?Side 2:TTS Ltd/Logo/Graphic?Brogan & Co.Name:Address:Phone:Email:The design is mostly flexible but must incorporate a Phoenix.For example "Tarwick & Co." with a block phoenix behind the text...up to you.

Industry/Entity Type

Telecommunications

Contact Information for Business Card

Tarwick & Co.
Address:
Name:
Phone:
Email:

Logo Text

Tarwick & Co.

Colors
33a6d7
0792cd
acd037
9bcb3c
f78f20
fece3e

Requirements
Must have
• Phoenix
• 3/4 colours max
• Blue representing Technology (wireless)
• Green for Eco Energy
• Orange for Phoenix
• White business card background
Should not have
• phoenix must not all be red/ orange fire, we are a technology service company and the phoenix colours must represent this. Fire is not representative of our company.

```html
<!DOCTYPE html>
<html lang="en">
<head>
<meta charset="utf-8">
<title>Tarwick &amp; Co. — Business Card</title>
<link href="https://fonts.googleapis.com/css2?family=Work+Sans:wght@300;400;600&display=swap" rel="stylesheet">
<style>
  :root {
    --backdrop: #e4e7ea;
    --card: #ffffff;
    --card-edge: #d6dadd;
    --brand-blue: #0792cd;
    --brand-blue-light: #33a6d7;
    --brand-green: #9bcb3c;
    --brand-orange: #f78f20;
    --ink: #2a2a2a;
    --ink-soft: #6b6b6b;
  }
  * { margin: 0; padding: 0; box-sizing: border-box; }
  html, body {
    width: 1200px; height: 900px; overflow: hidden;
    background: var(--backdrop);
    font-family: "Work Sans", sans-serif;
  }
  .canvas {
    position: relative; width: 1200px; height: 900px;
    display: flex; flex-direction: column; align-items: center;
    justify-content: center; gap: 40px;
  }
  .card {
    position: relative; width: 700px; height: 400px;
    background: var(--card);
    border: 1px solid var(--card-edge);
    box-shadow: 0 14px 34px rgba(0,0,0,.14);
  }
  .wordmark {
    display: flex; align-items: center; gap: 18px;
    font-weight: 300; letter-spacing: 1px;
    color: var(--brand-blue);
    white-space: nowrap;
  }
  .wordmark-square { display: block; background: var(--brand-orange); }
  .card-front .wordmark {
    position: absolute; left: 50%; top: 50%;
    transform: translate(-50%, -50%);
    font-size: 66px;
  }
  .card-front .wordmark-square { width: 54px; height: 54px; }
  .card-back .wordmark {
    position: absolute; left: 40px; top: 150px;
    font-size: 44px;
  }
  .card-back .wordmark-square { width: 40px; height: 40px; }
  .divider {
    position: absolute; left: 372px; top: 70px;
    width: 2px; height: 240px; background: var(--brand-green);
  }
  .contact {
    position: absolute; left: 400px; top: 72px;
    color: var(--ink);
  }
  .contact-name {
    font-weight: 600; font-size: 24px; letter-spacing: 2px;
    text-transform: uppercase; color: var(--ink);
  }
  .contact-role { font-size: 16px; color: var(--brand-blue); margin-top: 2px; letter-spacing: .5px; }
  .contact-address { font-size: 17px; line-height: 24px; margin-top: 20px; letter-spacing: .8px; }
  .contact-lines { list-style: none; margin-top: 16px; }
  .contact-lines li {
    display: flex; align-items: center; gap: 12px;
    font-size: 17px; line-height: 27px; letter-spacing: .8px;
  }
  .contact-lines svg { width: 13px; height: 13px; flex: none; }
</style>
</head>
<body>
<main class="canvas">
  <section class="card card-front" aria-label="Card front">
    <div class="wordmark"><span class="wordmark-square"></span><span>tarwick&amp;co</span></div>
  </section>

  <section class="card card-back" aria-label="Card back">
    <div class="wordmark"><span class="wordmark-square"></span><span>tarwick&amp;co</span></div>
    <div class="divider"></div>
    <div class="contact">
      <p class="contact-name">Daniel Forde</p>
      <p class="contact-role">Director</p>
      <p class="contact-address">18-24 Marlowe Street<br>Sydney NSW 2000 Australia</p>
      <ul class="contact-lines">
        <li>
          <svg viewBox="0 0 16 16" fill="none" stroke="#0792cd" stroke-width="1.5"><path d="M4 1.5 L6.5 4.5 L5 6.5 Q6.5 9.5 9.5 11 L11.5 9.5 L14.5 12 L12.5 14.5 Q4 13 1.5 3.5 Z"/></svg>
          <span>+612&nbsp; 9450 3172</span>
        </li>
        <li>
          <svg viewBox="0 0 16 16" fill="#0792cd"><rect x="4" y="1" width="8" height="4"/><rect x="1" y="6" width="14" height="6" rx="1"/><rect x="4" y="11" width="8" height="4"/></svg>
          <span>+612&nbsp; 9450 3173</span>
        </li>
        <li>
          <svg viewBox="0 0 16 16" fill="none" stroke="#0792cd" stroke-width="1.4"><rect x="1.5" y="3.5" width="13" height="9"/><path d="M1.5 3.5 L8 9 L14.5 3.5"/></svg>
          <span>mail@tarco.com.au</span>
        </li>
        <li>
          <svg viewBox="0 0 16 16" fill="none" stroke="#0792cd" stroke-width="1.3"><circle cx="8" cy="8" r="6.5"/><ellipse cx="8" cy="8" rx="3" ry="6.5"/><path d="M1.5 8 H14.5"/></svg>
          <span>www.tarco.com.au</span>
        </li>
      </ul>
    </div>
  </section>
</main>
</body>
</html>
```